Fitness Equipment & Service

I want to make the card eye catching and fun. We are called Corvane Motion Limited and we are based in Wales. We sell, install and service all types of fitness equipment from Skipping ropes, right through the Dumbbells, Kettle bells and Barbells through to state of the art Treadmills, Running Machines and Strength Equipment. We also design and install changing room furniture and lockers.

TYPOGRAPHY
We would like to use Futrura. Futura has an appearance of efficiency and forwardness. The typeface is derived
from simple geometric forms (near-perfect circles, triangles and squares) and is based on strokes of
near-even weight, which are low in contrast. This is most visible in the almost perfectly round stroke of
the o, which is nonetheless slightly ovoid.
The lowercase has tall ascenders, which rise above the cap line. The uppercase
characters present proportions similar to those of classical Roman capitals.

TYPOGRAPHIC CONSIDERATIONS
No Strike though
No Horizontal Scaling
No Drop Shadows
No Effects
Never use less than 120% Leading

OUR CORPORATE COLOURS
BRAND GUIDELINES
We were thinking that our primary colour palette consists of the Acid Green (Pantone 382) and Process Black.

We work closely with tquarly Ltd and would like to include their name on the card somewhere. I have attached images of the other brands that we work with as an idea or the small icons I have included that illustrate what we do?. I have very kindly been given permission to use any of the images off the files that I have included below, so I hope these help. I will include these below. I would be open to suggestions if it made the card more striking Can you do it?
Updates

Hi All, Just wanted to add a few thoughts but you are the guys with the creative visions (thats why are here) We are based in Wales, UK and we would be open to lots of different ideas on a theme but must be eye catching, Bold and FUN. If you can or think that the Welsh or any dragon could be put in there then go for it (its not a must have) We have also added some ideas for colour but again its over to you!! GO FOR IT ! Thanks and look forward to your visions! Owen

Hi All, Just thought I would sen through the contact details that need to be on the card. (if you want to play around with icons instead of the wording twitter, Facebook, go for it): Corvane Motion Limited Owen Pritchard Managing Director Mob: +44 (0)7582 913 406 e-mail: sales@corvanemotion.co.uk Web: Corvanemotion.co.uk twitter: @motionLetterbin Facebook: Corvane Motion Limited

```html
<!DOCTYPE html>
<html lang="en">
<head>
<meta charset="utf-8">
<title>Corvane Motion Limited – Business Card</title>
<link href="https://fonts.googleapis.com/css2?family=Arimo:wght@400;700&display=swap" rel="stylesheet">
<style>
  :root {
    --backdrop: #e9e7e2;
    --card: #ffffff;
    --gold: #dcbb55;
    --gold-deep: #cfa93f;
    --navy: #1f2a7c;
    --ink: #141414;
    --edge: #d6d3cc;
  }
  * { margin: 0; padding: 0; box-sizing: border-box; }
  html, body {
    width: 1200px;
    height: 892px;
    overflow: hidden;
    background: var(--backdrop);
    font-family: "Arimo", Arial, sans-serif;
  }
  .business-card {
    position: absolute;
    left: 120px;
    top: 166px;
    width: 960px;
    height: 560px;
    background: var(--card);
    border: 1px solid var(--edge);
    border-radius: 6px;
    overflow: hidden;
  }
  .side-band {
    position: absolute;
    left: 0;
    top: 48px;
    width: 70px;
    height: 440px;
    background: var(--gold);
    border-radius: 0 34px 34px 0;
  }
  .brand-block {
    position: absolute;
    left: 100px;
    top: 80px;
    width: 320px;
  }
  .brand-disc {
    display: block;
    width: 240px;
    height: 240px;
    border-radius: 50%;
    background: var(--navy);
    margin-left: 20px;
  }
  .brand-name {
    margin-top: 28px;
    font-weight: 700;
    font-size: 30px;
    line-height: 1.2;
    letter-spacing: 1px;
    text-transform: uppercase;
    color: var(--navy);
  }
  .contact-panel {
    position: absolute;
    left: 451px;
    top: 39px;
    width: 471px;
    height: 398px;
    background: linear-gradient(160deg, var(--gold) 0%, var(--gold-deep) 100%);
    border-radius: 30px;
    padding: 36px 20px 0 16px;
  }
  .person-name {
    font-weight: 700;
    font-size: 46px;
    line-height: 1.2;
    color: var(--navy);
  }
  .person-role {
    font-size: 32px;
    line-height: 1.2;
    color: var(--ink);
  }
  .contact-list {
    list-style: none;
    margin-top: 46px;
  }
  .contact-item {
    display: flex;
    align-items: center;
    gap: 30px;
    height: 42px;
    font-size: 27px;
    line-height: 1.2;
    color: var(--ink);
  }
  .contact-icon {
    flex: none;
    width: 26px;
    height: 26px;
    margin-left: 14px;
  }
</style>
</head>
<body>
  <main class="business-card">
    <div class="side-band"></div>

    <section class="brand-block">
      <span class="brand-disc"></span>
      <p class="brand-name">Corvane Motion Limited</p>
    </section>

    <section class="contact-panel">
      <h1 class="person-name">Owen Pritchard</h1>
      <p class="person-role">Managing Director</p>
      <ul class="contact-list">
        <li class="contact-item">
          <svg class="contact-icon" viewBox="0 0 26 26" aria-hidden="true">
            <rect width="26" height="26" fill="#1f2a7c"/>
            <path d="M9 6 L11 10 L9.5 11.5 C10.5 13.5 12.5 15.5 14.5 16.5 L16 15 L20 17 L19 20 C13 20 6 13 6 7 Z" fill="#fff"/>
          </svg>
          <span>+44 (0)7582 913 406</span>
        </li>
        <li class="contact-item">
          <svg class="contact-icon" viewBox="0 0 26 26" aria-hidden="true">
            <rect width="26" height="26" fill="#1f2a7c"/>
            <rect x="5" y="8" width="16" height="11" fill="none" stroke="#fff" stroke-width="1.6"/>
            <path d="M5 8 L13 14 L21 8" fill="none" stroke="#fff" stroke-width="1.6"/>
          </svg>
          <span>sales@corvanemotion.co.uk</span>
        </li>
        <li class="contact-item">
          <svg class="contact-icon" viewBox="0 0 26 26" aria-hidden="true">
            <rect width="26" height="26" fill="#1f2a7c"/>
            <circle cx="13" cy="13" r="7" fill="none" stroke="#fff" stroke-width="1.6"/>
            <ellipse cx="13" cy="13" rx="3" ry="7" fill="none" stroke="#fff" stroke-width="1.2"/>
            <line x1="6" y1="13" x2="20" y2="13" stroke="#fff" stroke-width="1.2"/>
          </svg>
          <span>Corvanemotion.co.uk</span>
        </li>
        <li class="contact-item">
          <svg class="contact-icon" viewBox="0 0 26 26" aria-hidden="true">
            <rect width="26" height="26" fill="#1f2a7c"/>
          </svg>
          <span>@motionLetterbin</span>
        </li>
        <li class="contact-item">
          <svg class="contact-icon" viewBox="0 0 26 26" aria-hidden="true">
            <rect width="26" height="26" fill="#1f2a7c"/>
          </svg>
          <span>Corvane Motion Limited</span>
        </li>
      </ul>
    </section>
  </main>
</body>
</html>
```